Flat bootstrap design for existing site

I'm looking for a modern flat design based around an existing logo. This has to be a custom design (no external templates), and implemented into a bootstrap framework.

The logo is attached as 2 versions - choose whichever you want, that flows better with whatever design you choose.

Added screenshots of the existing site (currently using the default bootstrap layouts). Please make your designs around those pages in the screenshots (i.e. the homepage only has the postal code input and the header). The active page has 3 screenshots, because I wanted to illustrate the other states that would be visible (in the table rows).

This is a moving/junk removal website, just for some context.

Here's some example websites (flat designs) that I like, just to give you an idea of what I'm after.

https://www.plimvora.com/
https://dacklow.com/
https://trevanu.com/
https://quobrintal.com/en/

Coding

Coded - Design and coding required

Number of Pages Required

5+ page

Colors

Designer to choose colors to be used in the design.

Requirements
Must have
• It must be a modern/simple flat design, that is built around the existing logo (attached).
• It has to be implemented using bootstrap.

```html
<!DOCTYPE html>
<html lang="en">
<head>
<meta charset="utf-8">
<title>Brovak – Sign In</title>
<link href="https://fonts.googleapis.com/css2?family=Montserrat:wght@400;500;600&display=swap" rel="stylesheet">
<style>
  :root {
    --accent: #4cc9f3;
    --ink: #111111;
    --heading: #444444;
    --muted: #9a9a9a;
    --page: #f6f6f8;
    --field-border: #dcdcdc;
    --footer: #e5e5e6;
    --footer-ink: #333333;
    --icon: #7a7a7a;
  }
  * { box-sizing: border-box; margin: 0; padding: 0; }
  html, body { width: 1200px; height: 658px; overflow: hidden; }
  body {
    position: relative;
    background: var(--page);
    font-family: "Montserrat", sans-serif;
    color: var(--ink);
    border-top: 3px solid var(--accent);
  }
  .brand {
    position: absolute; left: 99px; top: 34px;
    display: flex; align-items: center; gap: 10px;
    font-size: 36px; font-weight: 600; color: var(--accent);
    letter-spacing: 1px; text-decoration: none; line-height: 44px;
  }
  .brand-mark { width: 22px; height: 22px; border-radius: 50%; background: var(--accent); }
  .main-nav {
    position: absolute; top: 30px; right: 171px;
    display: flex; align-items: center;
  }
  .nav-link {
    font-size: 13px; font-weight: 500; text-transform: uppercase;
    color: var(--ink); text-decoration: none; line-height: 37px;
  }
  .nav-link.is-active { color: var(--accent); margin-right: 31px; }
  .nav-link.is-how { margin-right: 16px; }
  .nav-link.is-cta {
    background: var(--accent); color: #fff; border-radius: 2px;
    padding: 0 15px; margin-right: 16px;
  }
  .signin {
    position: absolute; left: 0; right: 0; top: 154px;
    display: flex; flex-direction: column; align-items: center;
  }
  .signin-title {
    font-size: 32px; font-weight: 500; color: var(--heading);
    letter-spacing: 1px; line-height: 40px; margin-bottom: 22px;
  }
  .field {
    position: relative; width: 287px; height: 41px; margin-bottom: 12px;
    background: #fff; border: 1px solid var(--field-border); border-radius: 2px;
  }
  .field input {
    width: 100%; height: 100%; border: 0; background: transparent;
    padding: 0 40px 0 19px; font-family: inherit; font-size: 12px; font-weight: 500;
  }
  .field input::placeholder { color: var(--muted); }
  .field-icon {
    position: absolute; right: 15px; top: 50%; transform: translateY(-50%);
    color: var(--muted); font-size: 10px; font-weight: 600;
  }
  .login-button {
    width: 150px; height: 41px; margin-top: 2px; border: 0; border-radius: 2px;
    background: var(--accent); color: #fff;
    font-family: inherit; font-size: 17px; font-weight: 500; letter-spacing: 1px;
  }
  .scene {
    position: absolute; left: 237px; top: 375px; width: 726px; height: 225px;
    background: linear-gradient(180deg, rgba(229,233,238,0) 0%, #e3e8ec 45%, #dfe3e6 100%);
  }
  .site-footer {
    position: absolute; left: 0; right: 0; bottom: 0; height: 58px;
    background: var(--footer);
  }
  .social { position: absolute; left: 103px; top: 23px; display: flex; gap: 22px; }
  .social-dot { width: 11px; height: 11px; border-radius: 50%; background: var(--icon); }
  .copyright {
    position: absolute; left: 857px; top: 21px;
    font-size: 11px; color: var(--footer-ink);
  }
</style>
</head>
<body>
  <a class="brand" href="#"><span class="brand-mark"></span>BROVAK</a>

  <nav class="main-nav">
    <a class="nav-link is-active" href="#">Book</a>
    <a class="nav-link is-how" href="#">How it works</a>
    <a class="nav-link is-cta" href="#">Become a driver</a>
    <a class="nav-link" href="#">Sign in</a>
  </nav>

  <main class="signin">
    <h1 class="signin-title">PLEASE SIGN IN</h1>
    <div class="field">
      <input type="email" placeholder="Email Address">
      <svg class="field-icon" width="12" height="10" viewBox="0 0 12 10" aria-hidden="true">
        <rect x="0.75" y="0.75" width="10.5" height="8.5" rx="1" fill="none" stroke="#9a9a9a" stroke-width="1.3"/>
        <path d="M1 1.5 L6 5.5 L11 1.5" fill="none" stroke="#9a9a9a" stroke-width="1.3"/>
      </svg>
    </div>
    <div class="field">
      <input type="password" placeholder="Password">
      <span class="field-icon">***</span>
    </div>
    <button class="login-button" type="submit">LOGIN</button>
  </main>

  <div class="scene" role="img" aria-label="Flat illustration of a recycling plant, forklift, boxes, rubble piles and a dump truck"></div>

  <footer class="site-footer">
    <div class="social">
      <span class="social-dot"></span>
      <span class="social-dot"></span>
      <span class="social-dot"></span>
      <span class="social-dot"></span>
    </div>
    <p class="copyright">Copyrights © 2017 - All Rights Reserved</p>
  </footer>
</body>
</html>
```